The Brightwater Hour (By Line: Making an Impact through Effective Leadership)

I am seeking the design and creation of a”banner ad image” for my radio program entitled “The Brightwater Hour.” The banner created should capture the look and feel of an image that reflects the vision statement below and that fosters the intent reflected by the principal goals listed below:

Vision statement

The Brightwater Hour is a powerfully engaging platform for great conversations about leadership and leadership learning.

Goals

1. Build a community of listeners who will be made to feel invited and excited about being connected to the show, it host and its broader community of listeners.

2. Provide interesting, intelligent and meaningful conversations about leadership and learning by the host, invited guests, both in studio and online.
The banner should be one that speaks to/invites listeners to become members of a community of listeners seeking to listen to and learn about the subject of leadership and leadership improvement.

The acceptable (final) banner should be professional in image, style and substance. The Photo shop layered file is required so that the banner image can be altered and adapted for use in PDF or text documents.

Finally, it is a banner that I intend to repopulate across several medium’s, such as pelzor, grip tally, etc. as a part of the process of establishing an image – brand – for the radio show as reflected the vision statement and goals.

While the target audience described is broad, it is anticipated that the primary listeners will be those who are leaders and serving in such roles as CEO’s, Vice Presidents, and other leaders in business, government and other local organizational capacities including students interested in learning about and discussing the subject of leadership.

Target Market(s)

Those who are interested in the topic of leadership and are actively engaged in leading as supervisors, managers and executives. These would be CEO, VP, and other C-level leaders in business, private and public sector organizations. It is also anticipated that those who are students of leadership learning will find my program a great resource.

Industry/Entity Type

Radio

Colors
3176b5
b768aa
d3a5cc

Requirements
Must have
• Be unique, attractive and capture the look and feel as noted in the description of the project.
Nice to have
• Note: I will have a head shot photo included in the banner so a place holder needs to be included for that

```html
<!DOCTYPE html>
<html lang="en">
<head>
<meta charset="utf-8">
<title>The Brightwater Hour – Banner</title>
<link rel="stylesheet" href="https://fonts.googleapis.com/css2?family=Open+Sans:wght@600;700&family=Source+Sans+3:wght@300;400&display=swap">
<style>
  :root {
    --page-bg: #f2f2f2;
    --brand-blue: #3176b5;
    --brand-magenta: #b768aa;
    --brand-pink: #d3a5cc;
    --photo-light: #e8eef2;
    --photo-mid: #c9d3da;
    --photo-dark: #9ea7ae;
    --text-light: #ffffff;
  }
  html, body {
    margin: 0;
    width: 1200px;
    height: 1200px;
    overflow: hidden;
    background: var(--page-bg);
  }
  .banner {
    position: absolute;
    left: 60px;
    top: 150px;
    width: 1080px;
    height: 900px;
    display: block;
  }
  .vision-text {
    font-family: "Source Sans 3", sans-serif;
    font-weight: 400;
    font-size: 27px;
    fill: var(--text-light);
  }
  .cta-text {
    font-family: "Source Sans 3", sans-serif;
    font-weight: 300;
    font-size: 48px;
    fill: var(--text-light);
  }
  .title-text {
    font-family: "Open Sans", sans-serif;
    font-weight: 600;
    font-size: 54px;
    fill: var(--text-light);
  }
</style>
</head>
<body>
  <svg class="banner" viewBox="0 0 840 700" xmlns="http://www.w3.org/2000/svg">
    <defs>
      <linearGradient id="photo-tones" x1="0" y1="0" x2="1" y2="1">
        <stop offset="0" stop-color="var(--photo-light)"/>
        <stop offset="0.55" stop-color="var(--photo-mid)"/>
        <stop offset="1" stop-color="var(--photo-dark)"/>
      </linearGradient>
    </defs>

    <rect class="hero-photo" x="0" y="0" width="840" height="700" fill="url(#photo-tones)"
          role="img" aria-label="Photo of a smiling businesswoman in glasses reading a newspaper in a bright office (host headshot placeholder)"/>

    <polygon class="shape-blue" points="143,0 840,0 840,125 587,440" fill="var(--brand-blue)" opacity="0.93"/>
    <polygon class="shape-pink" points="398,700 598,456 840,700" fill="var(--brand-pink)" opacity="0.92"/>
    <polygon class="shape-magenta" points="840,135 594,446 840,700" fill="var(--brand-magenta)" opacity="0.9"/>

    <text class="vision-text" text-anchor="middle">
      <tspan x="567" y="108">The Brightwater Hour is a power-</tspan>
      <tspan x="567" y="143">fully engaging platform for great</tspan>
      <tspan x="567" y="178">conversations about leadership</tspan>
      <tspan x="567" y="213">and leadership learning.</tspan>
    </text>

    <text class="cta-text" text-anchor="middle">
      <tspan x="748" y="428">LEARN</tspan>
      <tspan x="748" y="486">MORE</tspan>
    </text>

    <rect class="title-bar" x="132" y="548" width="576" height="90" fill="var(--brand-blue)" opacity="0.93"/>
    <text class="title-text" x="420" y="611" text-anchor="middle">Brightwater Hour</text>
  </svg>
</body>
</html>
```